STOREFRONT LIT SIGN for The Cantera Workshop

A sign advertising our music academy. This sign will be hung 10 feet above the entrance of our building and will be seen by all pedestrian and vehicle traffic on Fenwick Lane Delano.

Target Market(s)

Street passerby

Industry/Entity Type

Music Training

Font styles to use
Other font styles liked:
• Creative

Colors

Designer to choose colors to be used in the design.

Requirements
Must have
• A White Background
• Dimensions: 8 ft long x 3 ft tall
• The Cantera Workshop of Delano
• Lecciones de Piano, Violin, Guitarra, Voz, Trompeta y Mas
• MUSIC ACADEMY *(This should be most prominent)
• Guitar, Voice, Trumpet and More
• (555) 384-7291
• thecanteraworkshop.example
Nice to have
• Graphics of a piano, or guitar, or violin or trumpet or a combination of two or more

```html
<!DOCTYPE html>
<html lang="en">
<head>
<meta charset="utf-8">
<title>The Cantera Workshop – Storefront Sign Options</title>
<link href="https://fonts.googleapis.com/css2?family=Montserrat:ital,wght@0,500;0,600;0,700;1,600&family=Bebas+Neue&display=swap" rel="stylesheet">
<style>
  :root {
    --maroon: #641b35;
    --maroon-tint: #ead8df;
    --keys-tint: #c9a9b4;
    --ink: #111111;
    --paper: #ffffff;
    --board: #9a9c99;
  }
  html, body {
    margin: 0;
    padding: 0;
    width: 1200px;
    height: 865px;
    overflow: hidden;
    background: var(--board);
    font-family: "Montserrat", Arial, sans-serif;
  }
  .option-label {
    position: absolute;
    left: 52px;
    width: 100px;
    text-align: center;
    font-weight: 600;
    font-size: 92px;
    line-height: 1;
    color: var(--maroon);
  }
  .option-label.a { top: 192px; }
  .option-label.b { top: 600px; }

  .sign {
    position: absolute;
    left: 235px;
    width: 907px;
    height: 340px;
    background: var(--paper);
    overflow: hidden;
  }
  .sign.a { top: 50px; }
  .sign.b { top: 478px; }

  .sign-art {
    position: absolute;
    inset: 0;
  }
  .line {
    position: absolute;
    left: 0;
    width: 940px;
    text-align: center;
    line-height: 1;
    white-space: nowrap;
  }
  .studio-name {
    top: 24px;
    font-size: 50px;
    font-weight: 600;
    letter-spacing: -0.3px;
    color: var(--maroon);
  }
  .lessons {
    top: 83px;
    font-size: 16px;
    font-weight: 600;
    font-style: italic;
    color: var(--maroon);
  }
  .academy {
    font-weight: 600;
    color: var(--ink);
  }
  .sign.a .academy {
    top: 124px;
    font-size: 64px;
  }
  .sign.b .academy {
    top: 108px;
    font-family: "Bebas Neue", Impact, sans-serif;
    font-weight: 400;
    font-size: 98px;
    letter-spacing: 4px;
  }
  .instruments-line {
    font-size: 31px;
    font-weight: 500;
    color: var(--ink);
  }
  .sign.a .instruments-line { top: 193px; }
  .sign.b .instruments-line { top: 201px; }
  .phone {
    position: absolute;
    left: 277px;
    top: 243px;
    width: 372px;
    height: 56px;
    line-height: 56px;
    text-align: center;
    font-size: 46px;
    font-weight: 600;
    color: var(--paper);
  }
  .web {
    top: 303px;
    font-size: 16px;
    font-weight: 600;
    letter-spacing: 2.6px;
    color: var(--maroon);
  }
</style>
</head>
<body>

<div class="option-label a">A</div>
<div class="option-label b">B</div>

<section class="sign a">
  <svg class="sign-art" width="907" height="340" viewBox="0 0 907 340">
    <path d="M0,0 L154,0 Q210,170 81,340 L0,340 Z" fill="var(--maroon)"/>
    <path d="M106,0 Q160,170 44,340" fill="none" stroke="var(--paper)" stroke-width="6"/>
    <rect x="18" y="26" width="96" height="292" rx="40" fill="rgba(255,255,255,0.88)" role="img" aria-label="White treble clef illustration"/>
    <rect x="277" y="243" width="372" height="56" rx="16" fill="var(--maroon)"/>
    <rect x="735" y="198" width="104" height="142" fill="var(--maroon-tint)" role="img" aria-label="Illustration of a guitar, violin and trumpet in maroon silhouette"/>
    <rect x="839" y="0" width="68" height="340" fill="var(--keys-tint)" role="img" aria-label="Illustration of piano keys running down the right edge"/>
  </svg>
  <div class="line studio-name">The Cantera Workshop</div>
  <div class="line lessons">Lecciones de Piano, Violin, Guitarra, Voz, Trompeta y Mas</div>
  <div class="line academy">MUSIC ACADEMY</div>
  <div class="line instruments-line">Guitar, Voice, Trumpet and more</div>
  <div class="phone">(555) 384-7291</div>
  <div class="line web">thecanteraworkshop.example</div>
</section>

<section class="sign b">
  <svg class="sign-art" width="907" height="340" viewBox="0 0 907 340">
    <path d="M0,0 L154,0 Q210,170 81,340 L0,340 Z" fill="var(--maroon)"/>
    <path d="M106,0 Q160,170 44,340" fill="none" stroke="var(--paper)" stroke-width="6"/>
    <rect x="18" y="26" width="96" height="292" rx="40" fill="rgba(255,255,255,0.88)" role="img" aria-label="White treble clef illustration"/>
    <rect x="277" y="243" width="372" height="56" rx="16" fill="var(--maroon)"/>
    <rect x="735" y="198" width="104" height="142" fill="var(--maroon-tint)" role="img" aria-label="Illustration of a guitar, violin and trumpet in maroon silhouette"/>
    <rect x="839" y="0" width="68" height="340" fill="var(--keys-tint)" role="img" aria-label="Illustration of piano keys running down the right edge"/>
  </svg>
  <div class="line studio-name">The Cantera Workshop</div>
  <div class="line lessons">Lecciones de Piano, Violin, Guitarra, Voz, Trompeta y Mas</div>
  <div class="line academy">MUSIC ACADEMY</div>
  <div class="line instruments-line">Guitar, Voice, Trumpet and more</div>
  <div class="phone">(555) 384-7291</div>
  <div class="line web">thecanteraworkshop.example</div>
</section>

</body>
</html>
```